Dynamic Business Card for Sports Supplements Company

Hi! I'm looking for an awesome business card to match my existing sports supplement company. I have uploaded my current company logo and screenshot of the front page of my website.

I would like to have something dynamic and interesting and utilize the colors in the website - the reds and purples

The business card should be double sided and focus on a unique eye-catching design on the back and include all the relevant company info.

Most importantly, it should say somewhere: "Sign up on our website for a coupon code."

Target Market(s)

Mostly for women gym goers but it shouldn't be too feminine. It should be in keeping with the website design. It should flow and clearly be connected to it

Industry/Entity Type

Business

Contact Information for Business Card

Lorraine K. Vestal
CEO
LVestal@Quorvanexco.com
www.quorvanexco.com
555.417.3820
P.O. Box 47315
Alder, Montana 00000

Sign up on our website for a coupon code

Font styles to use
Serif
Sans Serif
Other font styles liked:
• Novecento font family and "Quorvanex" is in AR Destine font

Requirements
Must have
• One side should be a bold Quorvanex logo design. Even just the symbol itself may be o.k. (see attached file)

```html
<!DOCTYPE html>
<html lang="en">
<head>
<meta charset="utf-8">
<title>Quorvanex Business Card</title>
<link rel="stylesheet" href="https://fonts.googleapis.com/css2?family=Saira:wght@500;600;700&family=Open+Sans:wght@400;600&display=swap">
<style>
  :root {
    --brand-red: #e8202a;
    --ink: #1c1c1e;
    --paper: #f7f7f7;
    --charcoal: #222326;
    --charcoal-deep: #141517;
    --stage: #e9e7e4;
    --white: #ffffff;
  }
  * { margin: 0; padding: 0; box-sizing: border-box; }
  html, body {
    width: 1200px; height: 900px; overflow: hidden;
    background: var(--stage);
    font-family: "Open Sans", Arial, sans-serif;
  }
  .stage { position: relative; width: 1200px; height: 900px; }

  .card {
    position: absolute;
    border-radius: 18px;
    overflow: hidden;
    box-shadow: 0 10px 30px rgba(0,0,0,0.18);
  }

  .wordmark {
    font-family: "Saira", Arial, sans-serif;
    font-weight: 700;
    line-height: 1;
    white-space: nowrap;
  }
  .tagline {
    font-family: "Saira", Arial, sans-serif;
    font-weight: 500;
    text-transform: uppercase;
    white-space: nowrap;
    line-height: 1.1;
  }

  /* Front side */
  .card-front {
    left: 238px; top: 60px; width: 554px; height: 345px;
    background: var(--paper);
  }
  .front-panel { position: absolute; inset: 0; }
  .front-brand { position: absolute; left: 36px; top: 34px; width: 324px; }
  .front-brand .wordmark { color: var(--brand-red); font-size: 44px; letter-spacing: 4.6px; }
  .front-brand .tagline { color: var(--ink); font-size: 14px; letter-spacing: 3.1px; margin-top: 1px; }

  .holder { position: absolute; left: 36px; top: 175px; }
  .holder-name {
    font-family: "Saira", Arial, sans-serif;
    font-weight: 500;
    color: var(--brand-red);
    font-size: 20px;
    letter-spacing: 2.6px;
    text-transform: uppercase;
    line-height: 1.1;
    white-space: nowrap;
  }
  .holder-title { color: var(--ink); font-size: 16px; font-weight: 600; margin-top: 4px; }

  .contact-list { position: absolute; left: 36px; top: 237px; list-style: none; }
  .contact-list li {
    display: flex; align-items: center; gap: 9px;
    color: var(--ink); font-size: 15px; height: 25px; white-space: nowrap;
  }
  .contact-list svg { width: 13px; height: 13px; flex: none; }

  .mail-address {
    position: absolute; right: 29px; top: 270px;
    text-align: right; color: var(--white); font-size: 15px; line-height: 21px;
    font-style: normal; white-space: nowrap;
  }

  /* Back side */
  .card-back {
    left: 458px; top: 518px; width: 558px; height: 344px;
    background: radial-gradient(ellipse at 50% 35%, #3a3b3f 0%, var(--charcoal) 45%, var(--charcoal-deep) 100%);
    text-align: center;
  }
  .back-brand { position: absolute; left: 0; right: 0; top: 206px; }
  .back-brand .wordmark { color: var(--white); font-size: 38px; letter-spacing: 3.6px; }
  .back-brand .tagline { color: var(--white); font-size: 12px; letter-spacing: 2.7px; margin-top: 1px; }
  .coupon-note {
    position: absolute; left: 0; right: 0; top: 288px;
    color: var(--white); font-size: 15px; white-space: nowrap;
  }
  .coupon-note .accent { color: var(--brand-red); }
</style>
</head>
<body>
<main class="stage">

  <section class="card card-front" aria-label="Business card front">
    <svg class="front-panel" width="554" height="345" viewBox="0 0 554 345" aria-hidden="true">
      <defs>
        <linearGradient id="panelShade" x1="0" y1="0" x2="1" y2="1">
          <stop offset="0" stop-color="#2b2c30"/>
          <stop offset="1" stop-color="#151619"/>
        </linearGradient>
      </defs>
      <polygon points="472,0 554,0 554,345 274,345" fill="url(#panelShade)"/>
    </svg>

    <div class="front-brand">
      <div class="wordmark">QUORVANEX</div>
      <div class="tagline">Your Strength Companion</div>
    </div>

    <div class="holder">
      <div class="holder-name">Lorraine K. Vestal</div>
      <div class="holder-title">CEO</div>
    </div>

    <ul class="contact-list">
      <li>
        <svg viewBox="0 0 16 16" aria-hidden="true"><path fill="#e8202a" d="M1 5c0-2 2-3 7-3s7 1 7 3v1h-4V5H5v1H1zM3 7h10l2 7H1z"/><circle cx="8" cy="10.5" r="1.8" fill="#f7f7f7"/></svg>
        555.417.3820
      </li>
      <li>
        <svg viewBox="0 0 16 16" aria-hidden="true"><rect x="1" y="3" width="14" height="10" fill="#e8202a"/><path d="M1 3l7 6 7-6" fill="none" stroke="#f7f7f7" stroke-width="1.4"/></svg>
        LVestal@Quorvanexco.com
      </li>
      <li>
        <svg viewBox="0 0 16 16" aria-hidden="true"><circle cx="8" cy="8" r="7" fill="#e8202a"/><path d="M4 5c2 0 3 1 3 3s-2 1-2 3M10 3c0 2 2 2 3 4M9 13c0-2 2-2 3-3" fill="none" stroke="#f7f7f7" stroke-width="1.2"/></svg>
        www.quorvanexco.com
      </li>
    </ul>

    <address class="mail-address">
      P.O. Box 47315<br>
      Alder, Montana 00000
    </address>
  </section>

  <section class="card card-back" aria-label="Business card back">
    <div class="back-brand">
      <div class="wordmark">QUORVANEX</div>
      <div class="tagline">Your Strength Companion</div>
    </div>
    <p class="coupon-note"><span class="accent">Sign up</span> on our website for a coupon code</p>
  </section>

</main>
</body>
</html>
```